Web Developer Needs a Business Card Design

I need a personal business card design that represents me as a web developer for potential employers. I would like the background to be a dark color on the front for contrast with my logo and name. The back will have all my information along with a smaller version of the logo. I want something with a modern look and feel, not too conservative. This will be used for potential employers and freelance work.

Industry/Entity Type

Business

Contact Information for Business Card

Front should have my logo and name. The back should have all my personal information which would include: name: Tom Varulek, phone: 570-614-3098, email: tomvarulek@quillbox.net, website url: www.tomvarulek.net, logo, web developer.

Font styles to use
Sans Serif

Requirements
Must have
• Must include my logo. The color palette base color will be the logo color.

```html
<!DOCTYPE html>
<html lang="en">
<head>
<meta charset="utf-8">
<title>Tom Varulek — Business Card</title>
<link rel="stylesheet" href="https://fonts.googleapis.com/css2?family=Jost:wght@400;500;700&family=Lato:wght@400;700&display=swap">
<style>
  :root {
    --teal: #5fcab1;
    --ink: #1d1d1d;
    --card-dark: #121212;
    --card-dark-edge: #1f1f1f;
    --card-light: #f7f7f5;
    --label: #333333;
    --mark-faint: #9a9a9a;
    --backdrop: #d9d9d9;
  }
  * { box-sizing: border-box; margin: 0; padding: 0; }
  html, body {
    width: 1200px;
    height: 1000px;
    overflow: hidden;
  }
  body {
    background: radial-gradient(ellipse at 50% 40%, #ececec 0%, var(--backdrop) 100%);
    display: flex;
    align-items: center;
    justify-content: center;
    gap: 50px;
    font-family: "Lato", sans-serif;
  }
  .card {
    position: relative;
    width: 540px;
    height: 309px;
    border-radius: 4px;
    overflow: hidden;
    box-shadow: 0 14px 30px rgba(0,0,0,0.25);
  }

  /* Front */
  .card--front {
    background:
      repeating-linear-gradient(45deg, rgba(255,255,255,0.025) 0 2px, transparent 2px 4px),
      repeating-linear-gradient(-45deg, rgba(255,255,255,0.025) 0 2px, transparent 2px 4px),
      linear-gradient(160deg, var(--card-dark-edge), var(--card-dark));
  }
  .front__mark {
    position: absolute;
    left: 205px;
    top: 34px;
    width: 130px;
    height: 130px;
  }
  .front__name {
    position: absolute;
    left: 0;
    right: 0;
    top: 190px;
    text-align: center;
    font-family: "Jost", sans-serif;
    font-weight: 700;
    font-size: 52px;
    letter-spacing: 0.5px;
    color: var(--teal);
  }

  /* Back */
  .card--back {
    background: var(--card-light);
  }
  .back__mark {
    position: absolute;
    left: 150px;
    top: 150px;
    width: 150px;
    height: 150px;
  }
  .back__identity {
    position: absolute;
    left: 34px;
    top: 34px;
  }
  .back__name {
    font-family: "Jost", sans-serif;
    font-weight: 700;
    font-size: 40px;
    line-height: 1;
    color: var(--teal);
  }
  .back__role {
    margin-top: 8px;
    font-family: "Jost", sans-serif;
    font-weight: 500;
    font-size: 13px;
    letter-spacing: 1.2px;
    text-transform: uppercase;
    color: var(--ink);
  }
  .back__role .divider {
    display: inline-block;
    width: 2px;
    height: 12px;
    margin: 0 5px -1px;
    background: var(--ink);
  }
  .contact {
    position: absolute;
    left: 240px;
    top: 130px;
    list-style: none;
    font-size: 17px;
    line-height: 1;
  }
  .contact__item + .contact__item { margin-top: 16px; }
  .contact__label { color: var(--label); }
  .contact__value { color: var(--teal); }
</style>
</head>
<body>

  <section class="card card--front" aria-label="Card front">
    <svg class="front__mark" viewBox="0 0 130 130" aria-hidden="true">
      <circle cx="65" cy="65" r="62" fill="#2b2b2b"/>
      <circle cx="65" cy="65" r="50" fill="none" stroke="var(--teal)" stroke-width="8"/>
    </svg>
    <h1 class="front__name">Tom Varulek</h1>
  </section>

  <section class="card card--back" aria-label="Card back">
    <svg class="back__mark" viewBox="0 0 150 150" aria-hidden="true">
      <circle cx="75" cy="75" r="72" fill="var(--mark-faint)" opacity="0.35"/>
      <circle cx="75" cy="75" r="56" fill="none" stroke="var(--teal)" stroke-width="8" opacity="0.6"/>
    </svg>
    <div class="back__identity">
      <h2 class="back__name">Tom Varulek</h2>
      <p class="back__role">Logo<span class="divider"></span>Web Developer</p>
    </div>
    <ul class="contact">
      <li class="contact__item"><span class="contact__label">phone</span><span class="contact__value">570-614-3098</span></li>
      <li class="contact__item"><span class="contact__label">email</span><span class="contact__value">tomvarulek@quillbox.net</span></li>
      <li class="contact__item"><span class="contact__label">website</span><span class="contact__value">www.tomvarulek.net</span></li>
    </ul>
  </section>

</body>
</html>
```